IT support company needs Banner Ad for the top of their quote layout template

We need a banner Ad for the top of our for quote layout template so it is sent out on all our quotes

The banner size must be 827 x 100 pixels - anything larger than 60 KB can cause upload time issues

We have attached our logo and examples of the quote page to see how it looks in the context of the whole page.

Essential elements of the banner
- Must have our logo but this can be changed to be different colours if it makes the design work better i.e. Kelmor Wave could be all in white

Colours
- Can use all of our standard colours - Orange, Black, Grey and White

Images
- As a premium IT support company we deal with people and technology so would like to see both of these Incorporated into the banner i.e. people using technology These images could be watermarked or one colour effect.

Look and Feel
- Professional, friendly, people, technology, premium

Target Market
Small business owners and managers

Industry/Entity Type

It Company

```html
<!DOCTYPE html>
<html lang="en">
<head>
<meta charset="utf-8">
<title>Kelmor Wave – Banner and Work Estimate</title>
<link href="https://fonts.googleapis.com/css2?family=Archivo:wght@400;700;800&family=Arimo:ital,wght@0,400;0,700;1,400&display=swap" rel="stylesheet">
<style>
  :root {
    --bg: #f0f1f1;
    --white: #ffffff;
    --orange: #f26a10;
    --orange-deep: #e0520a;
    --orange-light: #ff8a2a;
    --black: #1c1a19;
    --ink: #222222;
    --grey: #646464;
    --grey-line: #8a8a8a;
    --grey-fill: #dedede;
    --rule: #b9b9b9;
  }
  * { margin: 0; padding: 0; box-sizing: border-box; }
  html, body { width: 1200px; height: 1200px; overflow: hidden; background: var(--bg); }
  body { position: relative; font-family: "Arimo", Arial, sans-serif; color: var(--ink); }

  .banner-hero { position: absolute; left: 114px; top: 84px; width: 964px; height: 116px; box-shadow: 0 4px 8px rgba(0,0,0,.18); }
  .divider { position: absolute; left: 112px; top: 237px; width: 975px; height: 2px; background: var(--rule); }

  .estimate-page { position: absolute; left: 330px; top: 267px; width: 540px; height: 757px; background: var(--white); box-shadow: 0 4px 10px rgba(0,0,0,.2); font-size: 8px; }
  .estimate-page .banner-mini { position: absolute; left: 0; top: 0; width: 540px; height: 65px; }
  .abs { position: absolute; }

  .sender-name { left: 29px; top: 94px; font-size: 14px; }
  .sender-lines { left: 28px; top: 118px; line-height: 13px; }
  .doc-title { right: 24px; top: 88px; font-family: "Archivo", Arial, sans-serif; font-weight: 700; font-size: 27px; color: var(--grey); letter-spacing: .3px; }

  table { border-collapse: collapse; }
  .meta-table { left: 311px; top: 142px; width: 210px; }
  .meta-table th, .meta-table td { border: 1px solid var(--grey-line); height: 16px; text-align: center; font-weight: 400; width: 50%; }
  .meta-table th { background: var(--grey-fill); }

  .box-head { background: var(--grey-fill); border: 1px solid var(--grey-line); height: 18px; line-height: 17px; padding-left: 11px; }
  .to-head { left: 26px; top: 219px; width: 210px; }
  .to-lines { left: 28px; top: 239px; line-height: 12.6px; }

  .desc { left: 26px; top: 327px; width: 495px; height: 82px; border: 1px solid var(--grey-line); }
  .desc .box-head { border: 0; border-bottom: 1px solid var(--grey-line); }
  .desc p { padding: 12px 11px; }

  .items { left: 26px; top: 435px; width: 495px; height: 196px; border: 1px solid var(--grey-line); }
  .items .col { position: absolute; top: 0; height: 171px; border-right: 1px solid var(--grey-line); }
  .items .c-desc { left: 0; width: 285px; }
  .items .c-qty { left: 285px; width: 38px; text-align: center; }
  .items .c-unit { left: 323px; width: 72px; text-align: right; }
  .items .c-amt { left: 395px; width: 99px; text-align: right; border-right: 0; }
  .items .head { height: 18px; line-height: 17px; background: var(--grey-fill); border-bottom: 1px solid var(--grey-line); text-align: center; }
  .items .c-desc .head { text-align: left; padding-left: 11px; }
  .items .rows { line-height: 12.8px; padding-top: 1px; }
  .items .c-desc .rows { padding-left: 11px; }
  .items .c-unit .rows, .items .c-amt .rows { padding-right: 2px; }
  .items .total { position: absolute; left: 0; top: 171px; width: 100%; height: 24px; border-top: 1px solid var(--grey-line); line-height: 23px; }
  .items .thanks { position: absolute; left: 0; width: 285px; text-align: center; font-style: italic; border-right: 1px solid var(--grey-line); }
  .items .total-label { position: absolute; left: 296px; letter-spacing: .5px; }
  .items .total-cur { position: absolute; left: 398px; }
  .items .total-sum { position: absolute; right: 4px; }

  .note { left: 28px; top: 660px; width: 492px; line-height: 11.5px; font-size: 7.6px; }
  .contact { left: 26px; top: 711px; width: 495px; text-align: center; line-height: 13px; }
</style>
</head>
<body>

<svg width="0" height="0" style="position:absolute" aria-hidden="true">
  <defs>
    <linearGradient id="photo-tone" x1="0" y1="0" x2="1" y2="1">
      <stop offset="0" stop-color="#6a4632"/>
      <stop offset=".45" stop-color="#2a2522"/>
      <stop offset="1" stop-color="#161414"/>
    </linearGradient>
    <linearGradient id="orange-tone" x1="0" y1="0" x2="1" y2="0">
      <stop offset="0" stop-color="#ff8a2a"/>
      <stop offset=".6" stop-color="#f26a10"/>
      <stop offset="1" stop-color="#e0520a"/>
    </linearGradient>
    <symbol id="brand-banner" viewBox="0 0 964 116">
      <rect width="964" height="116" fill="#ffffff"/>
      <polygon points="254,0 630,0 558,116 178,116" fill="url(#photo-tone)" role="img" aria-label="Close-up photo of a laptop keyboard"/>
      <polygon points="630,0 964,0 964,116 558,116" fill="url(#orange-tone)"/>
      <polygon points="800,0 964,0 964,60 880,116 720,116" fill="#ef6210" opacity=".55"/>
      <polygon points="900,0 964,0 964,116 930,116" fill="#d94e08" opacity=".5"/>
      <circle cx="40" cy="59" r="5" fill="#f26a10"/>
      <text x="52" y="66" font-family="Archivo, Arial, sans-serif" font-weight="800" font-size="19" fill="#1c1a19">Kelmor Wave</text>
      <text x="283" y="54" font-family="Archivo, Arial, sans-serif" font-weight="800" font-size="27" fill="#ffffff" letter-spacing="1">The East Anglia</text>
      <text x="286" y="82" font-family="Archivo, Arial, sans-serif" font-weight="800" font-size="27" fill="#f26a10" letter-spacing="1">IT Experts</text>
      <g fill="none" stroke="#ffffff" stroke-width="3" stroke-linecap="round" stroke-linejoin="round">
        <polyline points="651,32 656,37 665,27"/>
        <polyline points="651,59 656,64 665,54"/>
        <polyline points="651,86 656,91 665,81"/>
      </g>
      <g font-family="Archivo, Arial, sans-serif" font-weight="700" font-size="17" fill="#ffffff" letter-spacing=".6">
        <text x="671" y="39">Proactive Care</text>
        <text x="671" y="66">Round the Clock Maintenance</text>
        <text x="671" y="93">Live Help Desk Support</text>
      </g>
    </symbol>
  </defs>
</svg>

<svg class="banner-hero" viewBox="0 0 964 116" role="img" aria-label="Kelmor Wave banner"><use href="#brand-banner"/></svg>

<div class="divider"></div>

<main class="estimate-page">
  <svg class="banner-mini" viewBox="0 0 964 116" preserveAspectRatio="none" role="img" aria-label="Kelmor Wave banner"><use href="#brand-banner"/></svg>

  <div class="abs sender-name">[Company Name]</div>
  <div class="abs sender-lines">[Street Address]<br>[City, ST&nbsp; ZIP]<br>Phone: (000) 000-0000</div>
  <h1 class="abs doc-title">WORK ESTIMATE</h1>

  <table class="abs meta-table">
    <tr><th>ESTIMATE #</th><th>DATE</th></tr>
    <tr><td>2034</td><td>5/1/2014</td></tr>
  </table>

  <div class="abs box-head to-head">TO</div>
  <div class="abs to-lines">[Name]<br>[Company Name]<br>[Street Address]<br>[City, ST&nbsp; ZIP]<br>[Phone]</div>

  <section class="abs desc">
    <div class="box-head">DESCRIPTION OF WORK</div>
    <p>Use this section to describe the work to be done. Be very specific.</p>
  </section>

  <section class="abs items">
    <div class="col c-desc"><div class="head">ITEMIZED COSTS</div><div class="rows">Service Fee<br>Labor: 5 hours at $75/hr<br>Parts, including sales tax<br>New client discount</div></div>
    <div class="col c-qty"><div class="head">QTY</div><div class="rows">1<br>5<br>7</div></div>
    <div class="col c-unit"><div class="head">UNIT PRICE</div><div class="rows">200.00<br>75.00<br>12.95<br>(50.00)</div></div>
    <div class="col c-amt"><div class="head">AMOUNT</div><div class="rows">200.00<br>375.00<br>90.65<br>(50.00)<br>-&nbsp;&nbsp;<br>-&nbsp;&nbsp;<br>-&nbsp;&nbsp;<br>-&nbsp;&nbsp;<br>-&nbsp;&nbsp;<br>-&nbsp;&nbsp;<br>-&nbsp;&nbsp;<br>-&nbsp;&nbsp;<br>-&nbsp;&nbsp;</div></div>
    <div class="total">
      <span class="thanks">Thank you for your business!</span>
      <span class="total-label">TOTAL ESTIMATE</span>
      <span class="total-cur">$</span>
      <span class="total-sum">615.65</span>
    </div>
  </section>

  <p class="abs note">Note: This estimate is not a contract or a bill. It is our best guess at the total price to complete the work stated above, based upon our initial inspection. If prices change or additional parts and labor are required, we will inform you prior to proceeding with the work.</p>
  <p class="abs contact">To schedule a time for us to complete the work, or if you have any questions, please contact<br>[Name, Phone, email@address.com]</p>
</main>

</body>
</html>
```